New Business Card for our Indoor Golf Training Facility

We are looking for designs for a new business card for our indoor golf training facility. Attached is our logo, our logo with our slogan, and here is our elevator pitch (What makes us different from the others) not sure if all the info will fit on one card, maybe you can condense the elevator pitch? here is the info

Elevator Pitch
We work with serious golfers and those that want to be serious golfers…
to make you better, faster, at all phases of the game…
We use the same state-of-the-art technology as professional golfers…
which produces data sets that shows your improvement in real time.
Our facility is available 24/7 to our members, which allows you to improve on your time.

our website: www.birchpinlinks.com

Target Market(s)

Golfers

Font styles to use
Serif
Sans Serif

Colors
ec1f27
f59195
fbd4d5
919191
d3d3d3
1b1b1b

Requirements
Must have
• our logo or our logo with the slogan, elevator pitch (can be condensed or shortened)

```html
<!DOCTYPE html>
<html lang="en">
<head>
<meta charset="utf-8">
<title>Birch Pin Links – Business Card</title>
<link href="https://fonts.googleapis.com/css2?family=Open+Sans:wght@400;600;700&family=Lato:wght@400;700&display=swap" rel="stylesheet">
<style>
  :root {
    --red: #ec1f27;
    --card-red: #e93d35;
    --pink: #f59195;
    --grey: #919191;
    --light-grey: #d3d3d3;
    --ink: #1b1b1b;
    --white: #ffffff;
    --backdrop: #6a6a6a;
  }
  * { margin: 0; padding: 0; box-sizing: border-box; }
  html, body { width: 1200px; height: 802px; overflow: hidden; }
  body { background: var(--backdrop); position: relative; font-family: "Open Sans", sans-serif; }

  .card { position: absolute; top: 274px; width: 443px; height: 264px; background: var(--white); overflow: hidden; }
  .card--front { left: 136px; }
  .card--back { left: 624px; }

  /* Front */
  .brand { position: absolute; right: 34px; top: 66px; display: flex; flex-direction: column; align-items: flex-end; }
  .brand__name { font-weight: 700; font-size: 30px; line-height: 1; color: var(--red); letter-spacing: -0.2px; }
  .brand__tagline { font-size: 11.5px; line-height: 1.2; color: var(--red); margin-top: 5px; }

  .person { position: absolute; left: 27px; top: 169px; }
  .person__name { font-size: 17px; color: var(--red); line-height: 20px; }
  .person__role { font-size: 12.5px; color: var(--ink); line-height: 16px; }
  .rule { position: absolute; left: 142px; right: 31px; top: 194px; height: 1px; background: var(--grey); }

  .contact { position: absolute; left: 26px; top: 210px; font-size: 13px; color: var(--ink); line-height: 16px; }
  .contact__row { display: flex; align-items: center; gap: 3px; }
  .contact__row svg { width: 13px; height: 13px; flex: none; }
  .address { position: absolute; right: 31px; top: 210px; font-size: 13px; color: var(--ink); line-height: 16px; text-align: right; }
  .band { position: absolute; left: 0; right: 0; bottom: 0; height: 10px; background: var(--red); }

  /* Back */
  .pitch { position: absolute; left: 0; right: 0; top: 0; height: 213px; background: var(--card-red); color: var(--white); font-family: "Lato", sans-serif; text-align: center; }
  .pitch__title { font-weight: 700; font-size: 17px; line-height: 20px; margin-top: 51px; letter-spacing: 0.2px; }
  .pitch__para { font-size: 12.3px; line-height: 16px; margin-top: 7px; }
  .pitch__title + .pitch__para { margin-top: 16px; }
  .visit { position: absolute; left: 0; right: 0; bottom: 0; height: 51px; display: flex; align-items: center; justify-content: center; font-family: "Lato", sans-serif; font-size: 12.3px; color: var(--ink); gap: 4px; }
  .visit__url { color: var(--red); font-size: 15.5px; }
</style>
</head>
<body>
  <section class="card card--front">
    <div class="brand">
      <span class="brand__name">Birch Pin Links</span>
      <span class="brand__tagline">Train Smarter. Play Lower. Every Day.</span>
    </div>

    <div class="person">
      <p class="person__name">Daniel Whitford</p>
      <p class="person__role">Managing Director</p>
    </div>
    <div class="rule"></div>

    <div class="contact">
      <p class="contact__row">
        <svg viewBox="0 0 14 14" aria-hidden="true"><circle cx="7" cy="7" r="6" fill="none" stroke="#ec1f27" stroke-width="1.4"/><path d="M5 4.2c-.6.4-.7 1.4 0 2.6.8 1.4 1.9 2.4 3 2.9.7.2 1.3-.1 1.5-.6l-1-.9-.7.4c-.6-.3-1.3-1-1.7-1.7l.4-.7-.8-1.1z" fill="#ec1f27"/></svg>
        513-555-0186
      </p>
      <p class="contact__row">
        <svg viewBox="0 0 14 14" aria-hidden="true"><circle cx="7" cy="7" r="6.3" fill="#ec1f27"/><circle cx="7" cy="7" r="3.4" fill="none" stroke="#fff" stroke-width="1"/><path d="M3.6 7h6.8M7 3.6c-1.4 1.9-1.4 4.9 0 6.8M7 3.6c1.4 1.9 1.4 4.9 0 6.8" fill="none" stroke="#fff" stroke-width=".8"/></svg>
        www.birchpinlinks.com
      </p>
    </div>
    <div class="address">
      <p>1480 Meadow Creek Rd. Unit B3</p>
      <p>Fairbourne, OH 45099</p>
    </div>
    <div class="band"></div>
  </section>

  <section class="card card--back">
    <div class="pitch">
      <h2 class="pitch__title">ELEVATOR PITCH</h2>
      <p class="pitch__para">We work with serious golfers and those that want to be serious golfers…<br>to make you better, faster, at all phases of the game…</p>
      <p class="pitch__para">We use the same state-of-the-art technology as professional golfers…<br>which produces data sets that shows your improvement in real time.</p>
      <p class="pitch__para">Our facility is available 24/7 to our members, which allows<br>you to improve on your time.</p>
    </div>
    <p class="visit">Visit <span class="visit__url">www.birchpinlinks.com</span> for more details.</p>
  </section>
</body>
</html>
```